self serve frozen yogurt store

would like a postcard to use for promotional purposes. We are a self serve frozen business in Alder Ridge Shopping Center located in Wilmington, DE. We are opened 7 days a week. We offer 15 flavors and over 40 different toppings.

Industry/Entity Type

Store

```html
<!DOCTYPE html>
<html lang="en">
<head>
<meta charset="utf-8">
<title>Coolcup Frozen Yogurt – Postcard</title>
<link href="https://fonts.googleapis.com/css2?family=Fredoka:wght@500;600;700&family=Raleway:wght@500;700&display=swap" rel="stylesheet">
<style>
:root{
  --purple:#7a3f97;
  --green:#8cc63f;
  --orange:#f7941d;
  --paper:#ffffff;
  --line:#c9c9cf;
  --backdrop:#efe9e1;
}
*{box-sizing:border-box;margin:0;padding:0}
html,body{width:1200px;height:900px;overflow:hidden}
body{background:var(--backdrop);position:relative;font-family:"Fredoka",sans-serif}
.card{position:absolute;background:var(--paper);overflow:hidden;box-shadow:0 6px 18px rgba(0,0,0,.18)}

/* ---------- back side ---------- */
.card-back{left:40px;top:15px;width:595px;height:470px}
.back-photo{position:absolute;left:0;top:110px;width:295px;height:285px;
  background:radial-gradient(circle at 35% 60%,#fff 0,#f1f0ec 45%,#dcdad3 100%)}
.back-header{position:absolute;left:0;top:0;width:440px;height:160px}
.contact{position:absolute;left:20px;top:36px;color:#fff;font-family:"Raleway",sans-serif;font-weight:500;font-size:14px;line-height:27px;list-style:none}
.contact li{display:flex;align-items:center;gap:9px}
.contact svg{width:13px;height:13px;flex:none}
.stamp-box{position:absolute;left:443px;top:15px;width:122px;height:146px;border:1.5px solid var(--line)}
.offer{position:absolute;left:18px;top:162px;font-size:21px;font-weight:700;line-height:21px}
.offer .we{color:var(--green)}
.offer .row{display:flex;align-items:flex-end;gap:3px}
.offer .amp{color:var(--green);font-size:24px;width:22px}
.offer .over{color:var(--green);font-size:8px;width:22px}
.offer .orange{color:var(--orange)}
.offer .purple{color:var(--purple)}
.back-brand{position:absolute;left:158px;top:335px}
.back-brand .name{color:var(--purple);font-weight:700;font-size:24px;line-height:1}
.back-brand .tag{color:var(--purple);font-weight:600;font-size:10px;letter-spacing:.3px;margin-top:3px}
.address-lines{position:absolute;left:320px;top:205px;width:245px}
.address-lines span{display:block;height:1px;background:var(--line);margin-bottom:40px}

/* ---------- front side ---------- */
.card-front{left:555px;top:390px;width:605px;height:475px}
.front-swoosh{position:absolute;left:0;top:0;width:605px;height:230px}
.front-brand{position:absolute;left:25px;top:52px}
.front-brand .name{color:var(--purple);font-weight:700;font-size:48px;line-height:1}
.front-brand .tag{color:var(--purple);font-weight:600;font-size:18px;margin-top:8px;margin-left:4px;letter-spacing:.4px}
.open-days{position:absolute;left:370px;top:28px;font-weight:700;line-height:.95}
.open-days .l1{color:var(--purple);font-size:27px}
.open-days .l2{color:var(--green);font-size:52px;margin-left:30px}
.open-days .l3{color:var(--orange);font-size:26px;margin-left:68px}
.phone{position:absolute;left:378px;top:142px;color:var(--orange);font-weight:700;font-size:25px;transform:rotate(13deg);transform-origin:left top}
.location{position:absolute;left:38px;top:168px;color:var(--purple);font-weight:700;font-size:15px;transform:rotate(3.5deg);transform-origin:left top;white-space:nowrap}
.yogurt-photo{position:absolute;left:45px;top:212px;width:395px;height:208px;border-radius:6px;
  background:radial-gradient(ellipse at 50% 45%,#f6eef2 0,#e8e2dc 55%,#f4f4f4 100%)}
.social{position:absolute;left:462px;top:218px;color:var(--green);font-weight:600;font-size:25px;line-height:28px}
.front-bands{position:absolute;left:0;bottom:0;width:605px;height:110px}
</style>
</head>
<body>

<section class="card card-back" aria-label="Postcard back">
  <div class="back-photo" role="img" aria-label="Photo of a strawberry splashing into white cream"></div>
  <svg class="back-header" viewBox="0 0 440 160" preserveAspectRatio="none" aria-hidden="true">
    <path d="M0 0H440C390 80 260 105 0 140Z" fill="var(--purple)"/>
  </svg>
  <ul class="contact">
    <li><svg viewBox="0 0 12 12"><path d="M6 1L1 5.5V11H4.5V7.5H7.5V11H11V5.5Z" fill="#fff"/></svg>1820 Maple Hollow Road Wilmington, DE 19808</li>
    <li><svg viewBox="0 0 12 12"><path d="M3 1L5 3.5 4 5C4.6 6.6 5.6 7.6 7 8L8.5 7 11 9 9.5 11C5 10.5 1.5 7 1 2.5Z" fill="#fff"/></svg>(302) 555-0147</li>
    <li><svg viewBox="0 0 12 12"><g fill="none" stroke="#fff" stroke-width="1"><circle cx="6" cy="6" r="5"/><ellipse cx="6" cy="6" rx="2.2" ry="5"/><path d="M1 6H11M2 3.5H10M2 8.5H10"/></g></svg>www.coolcupyogurt.com</li>
  </ul>
  <div class="stamp-box" aria-hidden="true"></div>
  <div class="offer">
    <div class="we">We offer</div>
    <div class="row"><span class="amp">&amp;</span><span class="orange">15 flavors</span></div>
    <div class="row"><span class="over">OVER</span><span class="purple">40 different toppings.</span></div>
  </div>
  <div class="back-brand">
    <div class="name">Coolcup</div>
    <div class="tag">FROZEN YOGURT</div>
  </div>
  <div class="address-lines" aria-hidden="true"><span></span><span></span><span></span><span></span></div>
</section>

<section class="card card-front" aria-label="Postcard front">
  <svg class="front-swoosh" viewBox="0 0 605 230" preserveAspectRatio="none" aria-hidden="true">
    <defs>
      <linearGradient id="mist" x1="0" y1="0" x2="0" y2="1">
        <stop offset="0" stop-color="#dcdce0"/><stop offset="1" stop-color="#f7f7f8"/>
      </linearGradient>
    </defs>
    <rect width="605" height="230" fill="url(#mist)"/>
    <path d="M0 150C120 150 250 110 330 130 345 120 350 120 360 128 440 180 540 200 605 205V230H0Z" fill="#fff"/>
    <path d="M344 140C340 150 338 156 344 160 350 156 348 150 344 140Z" fill="#d8d8de"/>
  </svg>
  <div class="front-brand">
    <div class="name">Coolcup</div>
    <div class="tag">FROZEN YOGURT</div>
  </div>
  <div class="open-days">
    <div class="l1">opened</div>
    <div class="l2">7 days</div>
    <div class="l3">a week</div>
  </div>
  <div class="phone">302-555-0147</div>
  <div class="location">Alder Ridge Shopping Center Wilmington, DE 19808</div>
  <div class="yogurt-photo" role="img" aria-label="Photo of frozen yogurt cups topped with fruit, berries and cookies"></div>
  <div class="social">check us<br>out on<br>socialpage</div>
  <svg class="front-bands" viewBox="0 0 605 110" preserveAspectRatio="none" aria-hidden="true">
    <path d="M0 40C200 60 420 20 605 5V110H0Z" fill="var(--orange)"/>
    <path d="M0 50C200 70 420 32 605 20V110H0Z" fill="#fff"/>
    <path d="M0 55C200 78 420 40 605 28V110H0Z" fill="var(--green)"/>
    <path d="M0 72C200 92 420 55 605 45V110H0Z" fill="var(--purple)"/>
  </svg>
</section>

</body>
</html>
```